National online rug retailer needs a home page design

See the FloorNest logo and create a home page design around that color theme. Details are spelled out in word document uploaded below.

Apparently this website did not take my attachement showing the logo and basic requirements.  If you would send me your email address, I will send you the attachment directly.
Best regards,
Tom Vance
tvance@mrdcorp.example

Target Market(s)

The target market is home owners 25 to 75 years old with combined incomes over $100,000 per year.

Industry/Entity Type

Online

Requirements
Must have
• Lots of white space with black letters and creative use of red and possibly one other color. Would like a compelling call to action button.

```html
<!DOCTYPE html>
<html lang="en">
<head>
<meta charset="utf-8">
<title>FloorNest — Home</title>
<link href="https://fonts.googleapis.com/css2?family=Open+Sans:wght@400;600;700&display=swap" rel="stylesheet">
<style>
:root{
  --red:#e00c0c;
  --red-dark:#b80808;
  --ink:#222;
  --muted:#666;
  --line:#e2e2e2;
  --nav:#3a3a3a;
  --footer:#3f3f3f;
  --footer-bottom:#333;
  --canvas:#ebebeb;
  --white:#fff;
}
*{box-sizing:border-box;margin:0;padding:0}
html,body{width:1200px;height:2203px;overflow:hidden}
body{background:var(--canvas);font-family:"Open Sans",Arial,sans-serif;color:var(--ink)}
.page{position:relative;width:980px;height:2203px;margin:0 auto;background:var(--white)}
a{color:inherit;text-decoration:none}

/* header */
.header{position:absolute;top:0;left:0;right:0;height:129px}
.brand{position:absolute;left:24px;top:44px;display:flex;align-items:center;gap:8px}
.brand-mark{width:22px;height:22px;background:var(--red)}
.brand-name{font-size:40px;font-weight:600;color:var(--red);letter-spacing:-1px;line-height:1}
.tagline{position:absolute;left:106px;top:99px;font-size:11px;color:var(--muted)}
.search{position:absolute;left:306px;top:78px;display:flex}
.search input{width:327px;height:34px;border:1px solid #ccc;padding:0 8px;font:12px "Open Sans",sans-serif;color:#999}
.search button{width:36px;height:34px;border:0;background:var(--red);display:flex;align-items:center;justify-content:center}
.top-links{position:absolute;right:24px;top:47px;font-size:11.5px;color:#555;text-align:right;line-height:1}
.top-links .cart b{color:var(--ink);font-weight:600}
.phone{margin-top:12px;font-size:15px;color:#555}
.phone strong{color:var(--red);font-weight:600}
.account{margin-top:12px}

/* nav */
.nav{position:absolute;top:129px;left:0;right:0;height:53px;background:var(--nav);display:flex;padding-left:49px}
.nav a{height:53px;display:flex;align-items:center;padding:0 30px;color:#fff;font-size:13.5px;border-right:1px solid #2c2c2c}
.nav a.active{background:var(--red)}

/* hero */
.hero{position:absolute;top:191px;left:0;width:980px;height:364px;background:linear-gradient(180deg,#9b8470 0%,#c8bba8 40%,#d7cfc3 55%,#a5281f 80%,#7a3b30 100%)}
.hero-arrow{position:absolute;top:157px;width:31px;height:56px;display:flex;align-items:center;justify-content:center}
.hero-arrow.prev{left:32px;background:rgba(255,255,255,.45)}
.hero-arrow.next{right:32px;background:#111}

/* browse */
.browse{position:absolute;top:598px;left:5px;width:970px;height:397px;border:1px solid var(--line);border-radius:4px}
.sidebar{position:absolute;left:0;top:0;width:239px}
.sidebar h2{height:44px;background:var(--red);color:#fff;font-size:18px;font-weight:400;padding:8px 20px;border-radius:4px 4px 0 0}
.sidebar li{list-style:none;height:43.6px;border-bottom:1px solid var(--line);display:flex;justify-content:space-between;align-items:center;padding:0 15px 0 20px;font-size:12px;font-weight:700;color:#333}
.sidebar li span{font-weight:400;color:#666;font-size:14px}
.styles{position:absolute;left:243px;top:24px;display:grid;grid-template-columns:352px 352px;column-gap:22px;row-gap:22px}
.style-card{position:relative;height:157px;border-bottom:4px solid var(--red);display:flex}
.style-text{width:178px;padding:14px 16px}
.style-text h3{font-size:17px;font-weight:400;margin-bottom:10px}
.style-text p{font-size:10px;line-height:16px;font-weight:600;color:#333}
.btn{display:inline-flex;align-items:center;justify-content:center;background:var(--red);color:#fff;font-size:12px;font-weight:700}
.style-text .btn{position:absolute;left:18px;bottom:0;width:104px;height:36px}
.style-img{width:174px;height:153px}

/* products */
.section-head{position:absolute;top:1032px;left:30px;right:30px;display:flex;align-items:center;gap:12px}
.section-head h2{font-size:18px;font-weight:400;white-space:nowrap}
.section-head .rule{flex:1;height:6px;background:repeating-linear-gradient(90deg,#ddd 0 2px,transparent 2px 4px)}
.products{position:absolute;left:34px;top:1087px;display:grid;grid-template-columns:repeat(3,292px);column-gap:19px;row-gap:46px}
.product{position:relative;height:348px;border:1px solid #ddd;background:#fff;box-shadow:0 8px 6px -6px rgba(0,0,0,.25);padding:14px 14px 0;overflow:hidden}
.product-img{height:201px}
.product h3{margin-top:24px;font-size:16px;font-weight:400;color:#555;padding-left:10px}
.buy{display:flex;align-items:center;gap:20px;padding-left:10px;margin-top:12px}
.buy .btn{width:110px;height:34px;font-size:13px}
.price{line-height:1.1;font-size:17px}
.price s{color:#555}
.price b{display:block;color:var(--red);font-weight:400;padding-left:6px}
.ribbon{position:absolute;top:20px;left:-30px;width:130px;height:26px;background:#555;color:#fff;font-size:13px;font-weight:700;text-align:center;line-height:26px;transform:rotate(-45deg)}

/* footer */
.footer{position:absolute;top:1882px;left:0;width:980px;height:258px;background:var(--footer);color:#fff;padding:0 24px}
.footer-cols{display:flex;border-bottom:1px solid #777;height:48px;align-items:center;font-size:14px;color:#ddd}
.footer-cols div{width:221px}
.footer-cols div:nth-child(2){width:203px}
.footer-cols div:nth-child(3){width:203px}
.footer-body{display:flex;padding-top:13px}
.footer-body ul{list-style:none;font-size:12px;line-height:19px}
.footer-body ul:nth-child(1){width:221px;padding-left:0}
.footer-body ul:nth-child(2){width:203px}
.footer-body ul:nth-child(3){width:203px}
.pay{display:flex;flex-wrap:wrap;gap:6px;width:300px;padding-left:0}
.card{width:29px;height:19px;border-radius:2px;background:#ddd}
.badge-row{display:flex;gap:10px;margin-top:24px;align-items:center}
.seal{width:44px;height:44px;border-radius:50%;background:#c9a830}
.badge{width:58px;height:28px;background:#e8e8e8;border-radius:3px}
.copyright{position:absolute;top:2140px;left:0;width:980px;height:63px;background:var(--footer-bottom);color:#ccc;font-size:13px;display:flex;align-items:center;justify-content:center}
</style>
</head>
<body>
<div class="page">
  <header class="header">
    <a class="brand" href="#"><span class="brand-mark"></span><span class="brand-name">FloorNest</span></a>
    <div class="tagline">for domestic and heirloom values</div>
    <form class="search">
      <input type="text" value="Enter a keyword or item" aria-label="Search">
      <button type="button" aria-label="Search">
        <svg width="18" height="18" viewBox="0 0 18 18"><circle cx="7.5" cy="7.5" r="5.5" fill="none" stroke="#fff" stroke-width="2.2"/><line x1="11.5" y1="11.5" x2="16" y2="16" stroke="#fff" stroke-width="2.4"/></svg>
      </button>
    </form>
    <div class="top-links">
      <div class="cart">Items (0) &nbsp;<b>Total $0.00</b> &nbsp;View Cart &nbsp;| &nbsp;Checkout</div>
      <div class="phone">Order Toll-Free &nbsp;: &nbsp;<strong>1-800-555-0142</strong></div>
      <div class="account">My Account &nbsp;| &nbsp;Sign &nbsp;&#9679; Live Chat &nbsp;&#9679; Online</div>
    </div>
  </header>

  <nav class="nav">
    <a class="active" href="#">Home</a><a href="#">Selection guides</a><a href="#">Rug Care</a><a href="#">FAQ</a><a href="#">Return Policy</a><a href="#">Free Shipping</a><a href="#">Clearance Rugs</a>
  </nav>

  <section class="hero" role="img" aria-label="Rolled shag rugs in brown, cream and red on a wooden floor">
    <span class="hero-arrow prev"><svg width="10" height="14"><path d="M9 1 2 7l7 6z" fill="#fff"/></svg></span>
    <span class="hero-arrow next"><svg width="10" height="14"><path d="M1 1l7 6-7 6z" fill="#fff"/></svg></span>
  </section>

  <section class="browse">
    <aside class="sidebar">
      <h2>Browse</h2>
      <ul>
        <li>RUG THEME<span>+</span></li><li>COLOR WAY<span>+</span></li><li>SIZE<span>+</span></li><li>SHAPE<span>+</span></li>
        <li>FIBER CONTENT<span>+</span></li><li>MFGR. BRAND<span>+</span></li><li>MFGR.COLLECTION<span>+</span></li><li>PRICE<span>+</span></li>
      </ul>
    </aside>
    <div class="styles">
      <article class="style-card"><div class="style-text"><h3>TRADITIONAL</h3><p>It is a long established fact that a reader will be distracted a</p><a class="btn" href="#">READ MORE</a></div><div class="style-img" role="img" aria-label="Purple geometric rug" style="background:linear-gradient(135deg,#7a3d8f,#a35fb5)"></div></article>
      <article class="style-card"><div class="style-text"><h3>TRANSITIONAL</h3><p>It is a long established fact that a reader will be distracted a</p><a class="btn" href="#">READ MORE</a></div><div class="style-img" role="img" aria-label="Yellow shag rug with a green chair" style="background:linear-gradient(180deg,#b9b79a,#d8b43a)"></div></article>
      <article class="style-card"><div class="style-text"><h3>CASUAL</h3><p>It is a long established fact that a reader will be distracted a</p><a class="btn" href="#">READ MORE</a></div><div class="style-img" role="img" aria-label="White shag rug under a wooden table" style="background:linear-gradient(180deg,#6b5a4a,#e6e2dc)"></div></article>
      <article class="style-card"><div class="style-text"><h3>SIMPLE</h3><p>It is a long established fact that a reader will be distracted a</p><a class="btn" href="#">READ MORE</a></div><div class="style-img" role="img" aria-label="Stacked patterned rugs in tan and rust" style="background:linear-gradient(135deg,#a0643a,#d9b58a)"></div></article>
    </div>
  </section>

  <div class="section-head"><h2>FEATURE PRODUCTS</h2><span class="rule"></span>
    <svg width="24" height="12"><path d="M8 1 3 6l5 5M16 1l5 5-5 5" fill="none" stroke="#222" stroke-width="2"/></svg></div>

  <section class="products">
    <article class="product"><span class="ribbon">NEW</span><div class="product-img" role="img" aria-label="Black rug with colourful circles" style="background:linear-gradient(135deg,#2a1f1a,#5a3a2a)"></div><h3>Lorem Ipsum Dolor</h3><div class="buy"><a class="btn" href="#">ADD TO CART</a><div class="price"><s>$55.67</s><b>$48.67</b></div></div></article>
    <article class="product"><div class="product-img" role="img" aria-label="Grey patterned rug in a bright living room" style="background:linear-gradient(180deg,#d9d9d9,#9a9a9a)"></div><h3>Lorem Ipsum Dolor</h3><div class="buy"><a class="btn" href="#">ADD TO CART</a><div class="price"><s>$55.67</s><b>$48.67</b></div></div></article>
    <article class="product"><span class="ribbon">NEW</span><div class="product-img" role="img" aria-label="Cream rug with a red and black border" style="background:linear-gradient(135deg,#7a2a22,#e8dcc8 40%,#e8dcc8 60%,#7a2a22)"></div><h3>Lorem Ipsum Dolor</h3><div class="buy"><a class="btn" href="#">ADD TO CART</a><div class="price"><s>$55.67</s><b>$48.67</b></div></div></article>
    <article class="product"><div class="product-img" role="img" aria-label="Pale ornamental rug on a wooden floor" style="background:linear-gradient(180deg,#b08a5e,#e4ddcf)"></div><h3>Lorem Ipsum Dolor</h3><div class="buy"><a class="btn" href="#">ADD TO CART</a><div class="price"><s>$55.67</s><b>$48.67</b></div></div></article>
    <article class="product"><span class="ribbon">NEW</span><div class="product-img" role="img" aria-label="Red and grey swirl rug in front of a sofa" style="background:linear-gradient(180deg,#c9c3bb,#b53b32 40%,#ddd6cf)"></div><h3>Lorem Ipsum Dolor</h3><div class="buy"><a class="btn" href="#">ADD TO CART</a><div class="price"><s>$55.67</s><b>$48.67</b></div></div></article>
    <article class="product"><div class="product-img" role="img" aria-label="Red rug with curved lines on a wooden floor" style="background:linear-gradient(180deg,#d8cbb5,#a8231b)"></div><h3>Lorem Ipsum Dolor</h3><div class="buy"><a class="btn" href="#">ADD TO CART</a><div class="price"><s>$55.67</s><b>$48.67</b></div></div></article>
  </section>

  <footer class="footer">
    <div class="footer-cols"><div>Customer Services</div><div>Resources</div><div>Corporate Info</div><div>Payment &amp; Security</div></div>
    <div class="footer-body">
      <ul><li>Shipping</li><li>Return Policy</li><li>Privacy Policy</li><li>Ordering &amp; Delivery</li><li>Checklist</li><li>Terms of Use</li><li>Terms of Sale</li><li>Contact Us</li><li>Environmental Policy</li></ul>
      <ul><li>Product Articles</li><li>Learning Center</li><li>Help</li><li>Refer A Friend</li><li>FloorNest Blog</li><li>Room Scene Viewer</li><li>Site Map</li><li>FAQ</li><li>Customer Testimonials</li><li>Photo Gallery</li></ul>
      <ul><li>About FloorNest.com</li><li>Careers</li><li>Affiliates</li></ul>
      <div>
        <div class="pay" aria-label="Accepted payment methods"><span class="card"></span><span class="card"></span><span class="card"></span><span class="card"></span><span class="card"></span><span class="badge" style="width:100px"></span></div>
        <div class="badge-row" aria-label="Security certificates"><span class="seal"></span><span class="seal"></span><span class="badge"></span><span class="badge"></span><span class="badge"></span></div>
      </div>
    </div>
  </footer>
  <div class="copyright">© Copyrights 2013 &nbsp;FloorNest. All rights Reserved</div>
</div>
</body>
</html>
```